Garlic Farm for Farm Sales/Restaurant sales

Need a professional, but appealing to agriculture world. We are selling 27 kinds of Organic Garlic from a farm in Simla,CO. I have uploaded logo and business information-we are going to need a template, because I will need to use it for four separate people.
-We are trying to appeal to Farm to table restaurants
-As well as growers/farmers

Target Market(s)

Agriculture Sales/Restaurants-Organic

Industry/Entity Type

Agriculture

Contact Information for Business Card

Want it to look more unique then your average kelto stock card- I want it to look amazing

Font styles to use
Sans Serif

Colors
0455a3
ec1f27
fbed22
ffffff

Requirements
Must have
• Just be creative
Nice to have
• Colorful
Should not have
• plain

```html
<!DOCTYPE html>
<html lang="en">
<head>
<meta charset="utf-8">
<title>Prairie Clove Farm – Business Card</title>
<link rel="stylesheet" href="https://fonts.googleapis.com/css2?family=Source+Sans+3:wght@400;600&display=swap">
<style>
  :root {
    --page-bg: #ece9e6;
    --card-red: #c9283f;
    --card-red-dark: #b51f36;
    --ink-white: #ffffff;
    --brand-navy: #1d3a6e;
    --brand-red: #ec1f27;
    --frost-center: rgba(255, 255, 255, 0.92);
    --frost-edge: rgba(236, 232, 232, 0.85);
  }

  * { box-sizing: border-box; margin: 0; padding: 0; }

  html, body {
    width: 1200px;
    height: 900px;
    overflow: hidden;
    background: var(--page-bg);
    font-family: "Source Sans 3", sans-serif;
  }

  .business-card {
    position: absolute;
    left: 178px;
    top: 190px;
    width: 845px;
    height: 520px;
    border-radius: 18px;
    background: linear-gradient(160deg, var(--card-red) 0%, var(--card-red-dark) 100%);
    color: var(--ink-white);
    box-shadow: 0 14px 40px rgba(0, 0, 0, 0.12);
    overflow: hidden;
  }

  .person {
    position: absolute;
    left: 39px;
    top: 48px;
  }

  .person-name {
    font-size: 28px;
    font-weight: 600;
    line-height: 1.2;
  }

  .person-title {
    font-size: 22px;
    font-weight: 400;
    line-height: 1.3;
  }

  .address {
    position: absolute;
    left: 39px;
    top: 262px;
    font-size: 21px;
    line-height: 31px;
    font-style: normal;
  }

  .contact-list {
    position: absolute;
    left: 39px;
    top: 350px;
    list-style: none;
    font-size: 21px;
    line-height: 30px;
  }

  .contact-item {
    display: flex;
    align-items: center;
    gap: 11px;
  }

  .contact-item.web { font-size: 23px; }

  .contact-icon {
    width: 16px;
    height: 16px;
    flex: none;
    fill: var(--ink-white);
  }

  .brand-disc {
    position: absolute;
    left: 364px;
    top: 32px;
    width: 436px;
    height: 436px;
    border-radius: 50%;
    background: radial-gradient(circle at 50% 45%, var(--frost-center) 0%, var(--frost-edge) 100%);
    display: flex;
    flex-direction: column;
    align-items: center;
    justify-content: center;
    gap: 22px;
  }

  .brand-dot {
    width: 118px;
    height: 118px;
    border-radius: 50%;
    background: var(--brand-red);
  }

  .brand-name {
    font-size: 46px;
    font-weight: 600;
    line-height: 1.05;
    color: var(--brand-navy);
    text-align: center;
  }
</style>
</head>
<body>
  <section class="business-card" aria-label="Business card">
    <header class="person">
      <h1 class="person-name">Daniel Marsh</h1>
      <p class="person-title">Managing Director</p>
    </header>

    <address class="address">
      1234, Address GoesHere,<br>
      Country, 12345
    </address>

    <ul class="contact-list">
      <li class="contact-item">
        <svg class="contact-icon" viewBox="0 0 16 16" aria-hidden="true"><path d="M2 5c0-2 2-3 6-3s6 1 6 3v1h-3V5H5v1H2zM3 8l2-2h6l2 2v5H3zm5 1.2a1.6 1.6 0 1 0 0 3.2 1.6 1.6 0 0 0 0-3.2z"/></svg>
        (044) 123 456 789
      </li>
      <li class="contact-item">
        <svg class="contact-icon" viewBox="0 0 16 16" aria-hidden="true"><path d="M4 1h6l2 2v3h1a1 1 0 0 1 1 1v7a1 1 0 0 1-1 1H3a1 1 0 0 1-1-1V7a1 1 0 0 1 1-1h1zm1 1v4h6V3.5L9.5 2zm0 7v1h2V9zm3 0v1h2V9zm-3 2v1h2v-1zm3 0v1h2v-1z"/></svg>
        (044) 123456789
      </li>
      <li class="contact-item">
        <svg class="contact-icon" viewBox="0 0 16 16" aria-hidden="true"><path d="M1 3h14v10H1zm1.5 1.2V5l5.5 4 5.5-4v-.8L8 8z"/></svg>
        info@youremail.com
      </li>
      <li class="contact-item web">
        <svg class="contact-icon" viewBox="0 0 16 16" aria-hidden="true"><path d="M6.5 9.5l3-3 1 1-3 3zM7 4.5l2-2a3 3 0 0 1 4.5 4.5l-2 2-1-1 2-2a1.6 1.6 0 0 0-2.3-2.3l-2 2zm2 7l-2 2A3 3 0 0 1 2.5 9l2-2 1 1-2 2a1.6 1.6 0 0 0 2.3 2.3l2-2z"/></svg>
        www.websitename.com
      </li>
    </ul>

    <div class="brand-disc">
      <span class="brand-dot" aria-hidden="true"></span>
      <p class="brand-name">Prairie Clove Farm</p>
    </div>
  </section>
</body>
</html>
```